Social media agency for startUps! Need captivating web banner(s) needed

We need a few banners if Possible for a lead generation - branding campaign we are about to launch on Workvine & Chatterloop. We are Social media Agency created to help Startup and small medium business build there digital footprint. We also offer a brand analysing service to help brands understand there real time impact along with consulting, coaching and managed services. We are very open to the design concept. We are looking for creativity and professionalism. Something that will captivate and peek interest in learning more about how a company can work with us. We are need banners for Chatterloop and Workvine. If you require the formats please ask and we will send them. 2 for each platform would be nice, but depending on cost we would be happy with i for each network.

Designs should have our tag line : Accelerated Marketing. Refreshing Results. it should alsl speak to the fact that we are the Social Media Agency for Startups in Canada.

Target Market(s)

Small Medium Business and Start up companies

Industry/Entity Type

Media

Requirements
Must have
• company name - TrailMOSS Social
• out tag line - Accelerated Marketing. Refreshing Results
• our Logo -
• ad size -
• 160x600 Workvine
• 30x250 Workvine
• 1,200 x 628 pixels Chatterloop
• Recommended image size: 600 x 600 pixels
Nice to have
• This is the hard part - I would like to see something like a collage of all the social networks and how our brand connects them to the business in question. The other aspect could be something related to when you leveled up in a video game.
• i know this is somewhat vague, but i am open to any question you might have relating to this project.

```html
<!DOCTYPE html>
<html lang="en">
<head>
<meta charset="utf-8">
<title>TrailMOSS Social – Accelerated Marketing. Refreshing Results</title>
<link href="https://fonts.googleapis.com/css2?family=Bebas+Neue&family=Montserrat:wght@700&family=Open+Sans:wght@400&display=swap" rel="stylesheet">
<style>
  :root {
    --navy: #23222f;
    --orange: #f7931e;
    --orange-deep: #ef6a1a;
    --bullet-grey: #8d8c98;
    --white: #ffffff;
    --photo-light: #f1f1f3;
    --photo-mid: #dcdce0;
    --photo-skin: #e9d9cf;
  }
  html, body {
    margin: 0;
    padding: 0;
    overflow: hidden;
    background: var(--white);
  }
  .banner {
    position: relative;
    width: 1200px;
    height: 628px;
    overflow: hidden;
  }
  .banner__photo {
    position: absolute;
    inset: 0 0 0 470px;
    background:
      radial-gradient(ellipse 20% 16% at 62% 66%, rgba(236,40,120,0.35), transparent 75%),
      radial-gradient(ellipse 18% 14% at 38% 72%, rgba(255,200,0,0.35), transparent 75%),
      radial-gradient(ellipse 18% 14% at 78% 52%, rgba(120,200,40,0.3), transparent 75%),
      radial-gradient(ellipse 18% 14% at 72% 34%, rgba(30,160,230,0.3), transparent 75%),
      radial-gradient(ellipse 16% 12% at 50% 48%, rgba(240,90,40,0.3), transparent 75%),
      radial-gradient(ellipse 40% 50% at 90% 55%, var(--photo-skin), transparent 75%),
      radial-gradient(ellipse 35% 25% at 70% 50%, rgba(120,120,130,0.35), transparent 75%),
      linear-gradient(160deg, var(--photo-light) 0%, var(--photo-mid) 65%, #cfcfd4 100%);
  }
  .banner__panel {
    position: absolute;
    inset: 0;
    width: 600px;
    height: 628px;
  }
  .headline {
    position: absolute;
    left: 565px;
    top: 22px;
    margin: 0;
    font-family: "Bebas Neue", "Oswald", sans-serif;
    font-weight: 400;
    font-size: 58px;
    line-height: 65px;
    letter-spacing: 0.5px;
    color: var(--navy);
    text-transform: uppercase;
  }
  .brand {
    position: absolute;
    left: 30px;
    top: 52px;
    width: 380px;
    text-align: center;
  }
  .brand__mark {
    display: block;
    width: 92px;
    height: 92px;
    margin: 0 auto 30px;
    background: var(--orange);
  }
  .brand__name {
    margin: 0;
    font-family: "Montserrat", Arial, sans-serif;
    font-weight: 700;
    font-size: 31px;
    line-height: 38px;
    letter-spacing: 1px;
    color: var(--white);
    text-transform: uppercase;
    white-space: nowrap;
  }
  .brand__tagline {
    margin: 0;
    font-family: "Open Sans", Arial, sans-serif;
    font-size: 16px;
    line-height: 22px;
    letter-spacing: 0.6px;
    color: var(--white);
    white-space: nowrap;
  }
  .services {
    position: absolute;
    left: 36px;
    top: 284px;
    margin: 0;
    padding: 0;
    list-style: none;
  }
  .services__item {
    position: relative;
    padding-left: 32px;
    height: 56.5px;
    font-family: "Bebas Neue", "Oswald", sans-serif;
    font-weight: 400;
    font-size: 34px;
    line-height: 56px;
    color: var(--bullet-grey);
    text-transform: uppercase;
    letter-spacing: 0.3px;
    white-space: nowrap;
  }
  .services__item::before {
    content: "";
    position: absolute;
    left: 2px;
    top: 24px;
    width: 8px;
    height: 8px;
    border-radius: 50%;
    background: var(--bullet-grey);
  }
</style>
</head>
<body>
  <div class="banner">
    <div class="banner__photo" role="img" aria-label="Photo of a hand holding a smartphone with colourful app icons floating out of the screen"></div>

    <svg class="banner__panel" viewBox="0 0 600 628" aria-hidden="true">
      <defs>
        <linearGradient id="edgeGlow" x1="0" y1="0" x2="0" y2="1">
          <stop offset="0" stop-color="#f7931e"/>
          <stop offset="0.5" stop-color="#ef6a1a"/>
          <stop offset="1" stop-color="#f7931e"/>
        </linearGradient>
      </defs>
      <polyline points="484,0 594,314 484,628" fill="none" stroke="url(#edgeGlow)" stroke-width="6"/>
      <polygon points="0,0 478,0 588,314 478,628 0,628" fill="#23222f"/>
    </svg>

    <h1 class="headline">Accelerated Marketing.<br>Refreshing Results</h1>

    <div class="brand">
      <span class="brand__mark" aria-hidden="true"></span>
      <p class="brand__name">TrailMOSS Social</p>
      <p class="brand__tagline">Accelerated Marketing. Refreshing results</p>
    </div>

    <ul class="services">
      <li class="services__item">Brand Analysing Service</li>
      <li class="services__item">Consulting</li>
      <li class="services__item">Coaching &amp; Managed Services</li>
      <li class="services__item">Online Marketing</li>
      <li class="services__item">Social Media</li>
    </ul>
  </div>
</body>
</html>
```